Business Card Design needed for start up company Halvora

In need of a new business card designed for a start up company based in Sydney, Halvora is a new start up innovative Company, our mission it to make property accessible for everyday Australian and to become the leading Real Estate platform in Australia. We want it to be fresh and clean.

Industry/Entity Type

Financial

Contact Information for Business Card

Section for Name
Section for Title

HALVORA - The Strength of Pooling
Mobile:
Direct:

Font styles to use
Sans Serif

Colors
33a6d7
0692cd
0255a3
ffffff

Requirements
Must have
• Logo, all business card details

```html
<!DOCTYPE html>
<html lang="en">
<head>
<meta charset="utf-8">
<title>Halvora Business Card</title>
<link href="https://fonts.googleapis.com/css2?family=Montserrat:wght@800&family=Open+Sans:wght@400;600;700&display=swap" rel="stylesheet">
<style>
  :root {
    --page-bg: #1c1c1d;
    --card-bg: #38383a;
    --card-faint: #444446;
    --sky: #33a6d7;
    --sky-light: #5ec2ec;
    --ocean: #0692cd;
    --navy: #0255a3;
    --white: #ffffff;
    --muted: #c9c9cb;
  }
  * { box-sizing: border-box; margin: 0; padding: 0; }
  html, body { width: 1200px; height: 1000px; overflow: hidden; }
  body {
    background: var(--page-bg);
    font-family: "Open Sans", Arial, sans-serif;
    position: relative;
  }
  .card {
    position: absolute;
    left: 320px;
    width: 560px;
    height: 320px;
    border-radius: 22px;
    background: var(--card-bg);
    overflow: hidden;
    box-shadow: 0 14px 30px rgba(0,0,0,0.45);
  }
  .card--back { top: 150px; }
  .card--front { top: 530px; }

  .decor-circle {
    position: absolute;
    border-radius: 50%;
  }
  .card--back .decor-circle {
    width: 290px; height: 290px;
    right: 60px; top: 15px;
    background: var(--card-faint);
  }
  .card--front .decor-circle {
    width: 300px; height: 300px;
    right: 30px; top: 10px;
    background: linear-gradient(135deg, var(--sky-light), var(--sky));
  }

  .brand {
    position: absolute;
    display: flex;
    align-items: center;
    gap: 8px;
  }
  .brand__dot { border-radius: 50%; flex: none; }
  .brand__name {
    font-family: "Open Sans", Arial, sans-serif;
    font-weight: 700;
    letter-spacing: 0.5px;
    line-height: 1;
  }
  .card--back .brand { left: 26px; bottom: 30px; }
  .card--back .brand__dot { width: 38px; height: 38px; background: var(--sky); }
  .card--back .brand__name { font-size: 30px; color: var(--navy); }

  .card--front .brand { left: 30px; top: 34px; }
  .card--front .brand__dot { width: 42px; height: 42px; background: var(--white); }
  .card--front .brand__name { font-size: 32px; color: var(--white); }
  .tagline {
    position: absolute;
    left: 32px; top: 84px;
    font-size: 10.5px;
    letter-spacing: 2.6px;
    color: var(--white);
    text-transform: uppercase;
  }

  .person { position: absolute; left: 32px; top: 122px; }
  .person__name {
    font-size: 21px; font-weight: 600;
    color: var(--sky); letter-spacing: 0.8px;
    text-transform: uppercase; line-height: 1.1;
  }
  .person__title { font-size: 15px; color: var(--white); font-weight: 600; }

  .address {
    position: absolute; left: 32px; top: 182px;
    font-size: 12.5px; color: var(--muted); line-height: 1.35;
  }
  .contacts {
    position: absolute; left: 32px; top: 222px;
    list-style: none;
  }
  .contacts li {
    display: flex; align-items: center; gap: 9px;
    font-size: 13px; color: var(--white); line-height: 21px;
  }
  .contacts svg { width: 14px; height: 14px; flex: none; }
  .contacts .accent { color: var(--sky); }
</style>
</head>
<body>

<section class="card card--back" aria-label="Card back">
  <div class="decor-circle"></div>
  <div class="brand">
    <span class="brand__dot"></span>
    <span class="brand__name">HALVORA</span>
  </div>
</section>

<section class="card card--front" aria-label="Card front">
  <div class="decor-circle"></div>
  <div class="brand">
    <span class="brand__dot"></span>
    <span class="brand__name">HALVORA</span>
  </div>
  <p class="tagline">The Strength of Pooling</p>

  <div class="person">
    <p class="person__name">Elliot Marsh</p>
    <p class="person__title">Director</p>
  </div>

  <p class="address">48 Harbour Lane,<br>Sydney, 2000</p>

  <ul class="contacts">
    <li>
      <svg viewBox="0 0 14 14"><circle cx="7" cy="7" r="7" fill="#33a6d7"/><path d="M4.6 3.8l1.2 1.6-.7.8c.5 1 1.3 1.8 2.3 2.3l.8-.7 1.6 1.2-.6 1.2c-2.8-.3-5-2.5-5.3-5.3z" fill="#38383a"/></svg>
      <span>02 9417 3820</span>
    </li>
    <li>
      <svg viewBox="0 0 14 14"><circle cx="7" cy="7" r="7" fill="#33a6d7"/><rect x="5" y="3.5" width="4" height="7" rx="0.8" fill="none" stroke="#38383a" stroke-width="1"/></svg>
      <span>0412 586 903</span>
    </li>
    <li>
      <svg viewBox="0 0 14 14"><circle cx="7" cy="7" r="7" fill="#33a6d7"/><rect x="3.8" y="4.5" width="6.4" height="5" fill="none" stroke="#38383a" stroke-width="1"/><path d="M3.8 4.5L7 7.3l3.2-2.8" fill="none" stroke="#38383a" stroke-width="1"/></svg>
      <span>elliot@halvora.au</span>
    </li>
    <li>
      <svg viewBox="0 0 14 14"><circle cx="7" cy="7" r="7" fill="#33a6d7"/><circle cx="7" cy="7" r="3.3" fill="none" stroke="#38383a" stroke-width="1"/><path d="M3.7 7h6.6M7 3.7c-1.6 2-1.6 4.6 0 6.6M7 3.7c1.6 2 1.6 4.6 0 6.6" fill="none" stroke="#38383a" stroke-width="0.8"/></svg>
      <span>www.<span class="accent">halvora</span>.au</span>
    </li>
  </ul>
</section>

</body>
</html>
```